Business Card for a New Zealand IT Startup

I need a business card for VELTA Holdings. We are a young startup based in New Zealand working in internet marketing and web development. The design should have some element connected to New Zealand, such as wave, koru or silver fern, just don't use a kiwi bird.

```html
<!DOCTYPE html>
<html lang="en">
<head>
<meta charset="utf-8">
<title>VELTA Holdings – Business Card</title>
<link rel="stylesheet" href="https://fonts.googleapis.com/css2?family=Open+Sans:wght@400;700&display=swap">
<style>
  :root {
    --bg: #e9e7e4;
    --card-white: #eeeeee;
    --card-black: #141518;
    --pattern-mid: #2a2c31;
    --pattern-light: #4a4d54;
    --wave-dark: #3a3d44;
    --wave-light: #5c6069;
    --brand-blue: #1a6fc0;
    --brand-orange: #f26a2e;
    --ink: #3b3b3b;
    --divider: #b9b9b9;
  }
  * { box-sizing: border-box; margin: 0; padding: 0; }
  html, body { width: 1200px; height: 864px; overflow: hidden; }
  body {
    background: var(--bg);
    font-family: "Open Sans", Arial, sans-serif;
    position: relative;
  }
  .card {
    position: absolute;
    width: 540px;
    height: 309px;
    border-radius: 3px;
    box-shadow: 0 6px 18px rgba(0,0,0,0.18);
    overflow: hidden;
  }

  /* Back side */
  .card--back {
    left: 40px;
    top: 110px;
    background: var(--card-black);
  }
  .back-texture {
    position: absolute;
    inset: 0;
    background: radial-gradient(ellipse at 45% 35%, var(--pattern-light) 0%, var(--pattern-mid) 40%, var(--card-black) 85%);
  }
  .back-waves {
    position: absolute;
    left: 0;
    bottom: 0;
    width: 540px;
    height: 120px;
  }
  .back-waves__line {
    fill: none;
    stroke-width: 2;
  }
  .back-waves__line--dark { stroke: var(--wave-dark); }
  .back-waves__line--light { stroke: var(--wave-light); }
  .back-mark {
    position: absolute;
    right: 28px;
    bottom: 26px;
    display: flex;
    align-items: center;
    gap: 10px;
  }
  .back-mark__dot {
    width: 34px;
    height: 34px;
    border-radius: 50%;
    background: #d9d9d9;
  }
  .back-mark__name {
    color: #d9d9d9;
    font-weight: 700;
    font-size: 17px;
    letter-spacing: 0.5px;
  }

  /* Front side */
  .card--front {
    left: 620px;
    top: 440px;
    background: var(--card-white);
  }
  .brand {
    position: absolute;
    left: 22px;
    top: 112px;
    width: 268px;
    display: flex;
    align-items: center;
    justify-content: center;
    gap: 10px;
  }
  .brand__name {
    color: var(--brand-blue);
    font-weight: 700;
    font-size: 27px;
    letter-spacing: 0.3px;
    line-height: 1.1;
    white-space: nowrap;
  }
  .brand__dot {
    width: 24px;
    height: 24px;
    border-radius: 50%;
    background: var(--brand-blue);
    flex: none;
  }
  .brand-wave {
    position: absolute;
    left: 48px;
    top: 160px;
    width: 216px;
    height: 20px;
  }
  .brand-wave__line {
    fill: none;
    stroke: var(--brand-orange);
    stroke-width: 2.5;
    stroke-linecap: round;
  }
  .divider {
    position: absolute;
    left: 300px;
    top: 52px;
    width: 1px;
    height: 205px;
    background: var(--divider);
  }
  .contact {
    position: absolute;
    left: 316px;
    top: 54px;
    width: 210px;
    color: var(--ink);
    font-size: 12.5px;
    line-height: 1.45;
  }
  .contact__name {
    color: var(--brand-blue);
    font-weight: 700;
    font-size: 21px;
    line-height: 1.05;
    letter-spacing: 0.3px;
  }
  .contact__title {
    color: var(--brand-orange);
    font-size: 12.5px;
    letter-spacing: 0.5px;
    margin-bottom: 6px;
  }
  .contact__address { margin-bottom: 4px; }
  .contact__list { list-style: none; }
  .contact__item {
    display: flex;
    align-items: center;
    gap: 7px;
    white-space: nowrap;
  }
  .contact__icon {
    width: 12px;
    height: 12px;
    flex: none;
    fill: var(--brand-blue);
  }
</style>
</head>
<body>

  <section class="card card--back" aria-label="Card back">
    <div class="back-texture" role="img" aria-label="Glossy dark pattern of repeating wave swirls"></div>
    <svg class="back-waves" viewBox="0 0 540 120" aria-hidden="true">
      <path class="back-waves__line back-waves__line--dark" d="M0 40 Q45 20 90 40 T180 40 T270 40 T360 40 T450 40 T540 40"/>
      <path class="back-waves__line back-waves__line--light" d="M0 62 Q45 42 90 62 T180 62 T270 62 T360 62 T450 62 T540 62"/>
      <path class="back-waves__line back-waves__line--dark" d="M0 84 Q45 64 90 84 T180 84 T270 84"/>
    </svg>
    <div class="back-mark">
      <span class="back-mark__dot"></span>
      <span class="back-mark__name">VELTA Holdings</span>
    </div>
  </section>

  <section class="card card--front" aria-label="Card front">
    <div class="brand">
      <span class="brand__name">VELTA Holdings</span>
      <span class="brand__dot"></span>
    </div>
    <svg class="brand-wave" viewBox="0 0 216 20" aria-hidden="true">
      <path class="brand-wave__line" d="M2 10 Q20 2 38 10 T74 10 T110 10 T146 10 T182 10 T214 10"/>
    </svg>

    <div class="divider"></div>

    <div class="contact">
      <div class="contact__name">MARA TANE</div>
      <div class="contact__title">PRESIDENT</div>
      <div class="contact__address">27 Harbour View Road<br>Wellington 6011, NZ</div>
      <ul class="contact__list">
        <li class="contact__item">
          <svg class="contact__icon" viewBox="0 0 12 12" aria-hidden="true"><path d="M1 3c0-1 1-2 2-2h1l1 2-1 1c.5 1.5 1.5 2.5 3 3l1-1 2 1v1c0 1-1 2-2 2C4 10 1 7 1 3z"/></svg>
          <span>021 448 3917</span>
        </li>
        <li class="contact__item">
          <svg class="contact__icon" viewBox="0 0 12 12" aria-hidden="true"><path d="M3.5 0h5a1 1 0 0 1 1 1v10a1 1 0 0 1-1 1h-5a1 1 0 0 1-1-1V1a1 1 0 0 1 1-1zm.5 1.5v8h4v-8z"/></svg>
          <span>022 615 2704</span>
        </li>
        <li class="contact__item">
          <svg class="contact__icon" viewBox="0 0 12 12" aria-hidden="true"><path d="M3 0h6v3H3zM1 4h10a1 1 0 0 1 1 1v4H10v3H2V9H0V5a1 1 0 0 1 1-1zm2 5v2h6V9z"/></svg>
          <span>04 389 1265</span>
        </li>
        <li class="contact__item">
          <svg class="contact__icon" viewBox="0 0 12 12" aria-hidden="true"><path d="M0 2h12v1L6 7 0 3zm0 2.5 6 4 6-4V10H0z"/></svg>
          <span>mara@veltaholdings.com</span>
        </li>
        <li class="contact__item">
          <svg class="contact__icon" viewBox="0 0 12 12" aria-hidden="true"><circle cx="6" cy="6" r="6"/></svg>
          <span>www.veltaholdings.com</span>
        </li>
      </ul>
    </div>
  </section>

</body>
</html>
```